Simple Business Card Design for Tavlo

Job:

Make a very simple, minimalist business card design with my details including adjusted logo. One side to be white (with logo & text). Other side to be yellow - try plain or with logo (or part of logo eg Z). Need business card to have continuity with website.

Logo:
Our logo is made from a free download font website:
http://www.typewell.net/search.php?q=rubber
but the spacing/kerning needs correcting/adjusting as the font spaces unevenly between letters (see attached files). Need logo to be very crisp/sharp when printed.

Printing:
We will be using Plika.com so the design needs to conform to their requirements, see here:

http://uk.plika.com/products/luxe/business-cards.html (scroll down for dimensions and guidelines)

Design:

must say "plant-based food consulting" underneath logo or somewhere
no address needed in contact section
sharp corners (not rounded)
one side white, one side yellow

name: Rosalind Whitcombe
1xmobile number: +44 7700900463
1xtwiiter: @brimcounsel
website address www.orchardtable.com
email address brim@orchardtable.com

Should be easy quick job, prompt + detailed feedback given, am online in UK 9am-10pm for next 3 days. Website is www.orchardtable.com

Industry/Entity Type

Business

Requirements
Must have
• The logo must be corrected. The kerning is not right.

Please use a warm-grey for text

Please submit in matt format, we will be printing matt finish.

Should not have
• Avoid using banners or curvy highlights

Please avoid using black

Please avoid submitting in gloss finish

```html
<!DOCTYPE html>
<html lang="en">
<head>
<meta charset="utf-8">
<title>Tavlo – Business Card</title>
<link rel="stylesheet" href="https://fonts.googleapis.com/css2?family=Open+Sans:wght@400;600&display=swap">
<style>
  :root {
    --backdrop: #dcdcdc;
    --card-yellow: #f5e300;
    --card-white: #ffffff;
    --brand-yellow: #f2e000;
    --warm-grey: #3b3633;
    --paper-white: #ffffff;
  }
  * { box-sizing: border-box; margin: 0; padding: 0; }
  html, body {
    width: 1200px;
    height: 960px;
    overflow: hidden;
    background: var(--backdrop);
    font-family: "Open Sans", Arial, sans-serif;
  }
  .canvas {
    position: relative;
    width: 1200px;
    height: 960px;
  }
  .card {
    position: absolute;
    left: 260px;
    width: 680px;
    height: 440px;
    border-radius: 0;
    box-shadow: 0 6px 18px rgba(0,0,0,0.12);
    overflow: hidden;
  }
  .card--back {
    top: 30px;
    background: var(--card-yellow);
  }
  .card--front {
    top: 490px;
    background: var(--card-white);
  }
  .back-website {
    position: absolute;
    right: 40px;
    bottom: 34px;
    color: var(--paper-white);
    font-size: 19px;
    font-weight: 600;
    letter-spacing: 0.5px;
  }
  .brand-name {
    position: absolute;
    left: 44px;
    top: 14px;
    color: var(--brand-yellow);
    font-size: 118px;
    font-weight: 600;
    letter-spacing: 4px;
    line-height: 1;
  }
  .tagline {
    position: absolute;
    left: 48px;
    top: 148px;
    color: var(--warm-grey);
    font-size: 26px;
    font-weight: 400;
    line-height: 1.05;
  }
  .contact-block {
    position: absolute;
    right: 40px;
    bottom: 34px;
    color: var(--warm-grey);
  }
  .person-name {
    font-size: 22px;
    font-weight: 600;
    line-height: 1.2;
    margin-bottom: 12px;
  }
  .contact-list {
    list-style: none;
    font-size: 19px;
  }
  .contact-item {
    display: flex;
    align-items: center;
    gap: 12px;
    height: 30px;
  }
  .contact-icon {
    width: 20px;
    height: 20px;
    flex: none;
    fill: var(--warm-grey);
  }
  .contact-icon--at {
    font-size: 21px;
    font-weight: 600;
    line-height: 20px;
    text-align: center;
  }
</style>
</head>
<body>
<main class="canvas">

  <section class="card card--back" aria-label="Card back">
    <p class="back-website">www.orchardtable.com</p>
  </section>

  <section class="card card--front" aria-label="Card front">
    <h1 class="brand-name">Tavlo</h1>
    <p class="tagline">Plant-based<br>Food consulting</p>

    <div class="contact-block">
      <h2 class="person-name">Rosalind Whitcombe</h2>
      <ul class="contact-list">
        <li class="contact-item">
          <svg class="contact-icon" viewBox="0 0 24 24" aria-hidden="true">
            <path d="M6.6 10.8a15.1 15.1 0 0 0 6.6 6.6l2.2-2.2a1 1 0 0 1 1-.25 11.4 11.4 0 0 0 3.6.57 1 1 0 0 1 1 1V20a1 1 0 0 1-1 1A17 17 0 0 1 3 4a1 1 0 0 1 1-1h3.5a1 1 0 0 1 1 1c0 1.25.2 2.45.57 3.57a1 1 0 0 1-.25 1z"/>
          </svg>
          <span>+44 7700900463</span>
        </li>
        <li class="contact-item">
          <svg class="contact-icon" viewBox="0 0 24 24" aria-hidden="true">
            <circle cx="12" cy="12" r="8"/>
          </svg>
          <span>@brimcounsel</span>
        </li>
        <li class="contact-item">
          <svg class="contact-icon" viewBox="0 0 24 24" aria-hidden="true">
            <path d="M12 3 2 12h3v8h5v-5h4v5h5v-8h3z"/>
          </svg>
          <span>www.orchardtable.com</span>
        </li>
        <li class="contact-item">
          <span class="contact-icon contact-icon--at" aria-hidden="true">@</span>
          <span>brim@orchardtable.com</span>
        </li>
      </ul>
    </div>
  </section>

</main>
</body>
</html>
```